We are a recruitment company based in Norwich/Cambridge England.
I have included our company logo which we want to remain the same.

What we are looking for is a new creative Business card which will really stand out!!

Contact Information for Business Card

Harriet Dunmore
email: Harriet@plavex.co.uk
Address: Brackwell House
Fenmoor Enterprise Park
Partridge Way
Norwich
QB9 3KX
Tel:01632 960418

```html
<!DOCTYPE html>
<html lang="en">
<head>
<meta charset="utf-8">
<title>Plavex Business Card</title>
<link href="https://fonts.googleapis.com/css2?family=Montserrat:wght@400;500;600;700&display=swap" rel="stylesheet">
<style>
  :root {
    --backdrop: #e8e5e2;
    --card: #ffffff;
    --grey: #8c868d;
    --grey-dark: #6f6a70;
    --green: #8fcb1e;
    --line: #9a959b;
  }
  * { box-sizing: border-box; margin: 0; padding: 0; }
  html, body {
    width: 1200px;
    height: 997px;
    overflow: hidden;
    background: var(--backdrop);
    font-family: "Montserrat", sans-serif;
  }
  .stage {
    position: relative;
    width: 1200px;
    height: 997px;
  }
  .card {
    position: absolute;
    width: 500px;
    height: 286px;
    background: var(--card);
    box-shadow: 0 6px 18px rgba(0,0,0,0.10);
    overflow: hidden;
  }
  .card--front { left: 80px; top: 355px; }
  .card--back { left: 620px; top: 355px; }

  /* front */
  .side-band {
    position: absolute;
    left: 0; top: 0; bottom: 0;
    width: 72px;
    background: var(--grey);
    border-left: 4px solid var(--green);
  }
  .brand {
    position: absolute;
    display: flex;
    align-items: center;
    gap: 10px;
  }
  .brand__dot {
    border-radius: 50%;
    background: var(--green);
    flex: none;
  }
  .brand__name {
    font-weight: 600;
    color: var(--grey-dark);
    letter-spacing: 0.5px;
  }
  .card--front .brand { left: 46px; top: 30px; }
  .card--front .brand__dot { width: 40px; height: 40px; border: 4px solid #fff; }
  .card--front .brand__name { font-size: 34px; }

  .contact {
    position: absolute;
    left: 112px;
    top: 118px;
    color: var(--grey-dark);
    font-size: 13px;
    line-height: 1.55;
  }
  .contact__name {
    font-weight: 700;
    font-size: 14px;
    margin-bottom: 2px;
  }
  .contact__name .surname { color: var(--green); }
  .contact__row {
    display: flex;
    align-items: center;
    gap: 6px;
  }
  .contact__row svg { width: 11px; height: 11px; flex: none; }
  .contact__address { margin-top: 8px; }

  /* back */
  .card--back .brand {
    left: 50%;
    top: 104px;
    transform: translateX(-50%);
  }
  .card--back .brand__dot { width: 46px; height: 46px; }
  .card--back .brand__name { font-size: 40px; }
  .web {
    position: absolute;
    left: 0; right: 0;
    top: 192px;
    display: flex;
    align-items: center;
    justify-content: center;
    gap: 14px;
    font-size: 13px;
    font-weight: 600;
    color: var(--grey-dark);
    letter-spacing: 1px;
  }
  .web__rule {
    width: 80px;
    height: 1px;
    background: var(--line);
  }
</style>
</head>
<body>
<main class="stage">
  <section class="card card--front" aria-label="Business card front">
    <div class="side-band"></div>
    <div class="brand">
      <span class="brand__dot"></span>
      <span class="brand__name">Plavex</span>
    </div>
    <div class="contact">
      <p class="contact__name">Harriet <span class="surname">Dunmore</span></p>
      <p class="contact__row">
        <svg viewBox="0 0 12 12" aria-hidden="true"><path d="M2.5 1h2l1 3-1.3 1a6 6 0 0 0 2.8 2.8L8 6.5l3 1v2a1.5 1.5 0 0 1-1.5 1.5A8.5 8.5 0 0 1 1 2.5 1.5 1.5 0 0 1 2.5 1z" fill="var(--green)"/></svg>
        01632 960418
      </p>
      <p class="contact__row">
        <svg viewBox="0 0 12 12" aria-hidden="true"><rect x="0.5" y="2.5" width="11" height="7.5" rx="1" fill="var(--green)"/><path d="M1 3l5 4 5-4" stroke="#fff" stroke-width="1" fill="none"/></svg>
        Harriet@plavex.co.uk
      </p>
      <address class="contact__address" style="font-style:normal">
        Brackwell House<br>
        Fenmoor Enterprise Park<br>
        Partridge Way Norwich QB9 3KX
      </address>
    </div>
  </section>

  <section class="card card--back" aria-label="Business card back">
    <div class="brand">
      <span class="brand__dot"></span>
      <span class="brand__name">Plavex</span>
    </div>
    <p class="web">
      <span class="web__rule"></span>
      www.plavex.co.uk
      <span class="web__rule"></span>
    </p>
  </section>
</main>
</body>
</html>
```